Biz Card

MARKETING today is the most rapidly changing business discipline. Media options to reach customers, actual customer preferences and consumer buying decisions change by the minute . . . no, by the second. The behavioral data generated by all aspects of the business and the new technologies that put the data to work together produce the potential to generate business intelligence and guide smart resource allocation to influence purchase and retention. However, to realize this potential, marketing professionals at all levels and in all organizations must continuously improve their skills not just from on-the-job training but by learning from masters in the field. The Bright Horizon Guild is the training center that serves this professional development need.model logos:msi.orgama.orgcontentmarketinginstitute.comBook covers on MarketingMetrics, Marketing Anaytics
Industry/Entity Type
Business
Contact Information for Business Card
Roy A. YoungCEOMarketing Science Academyphone: 310-601-4755email: roy@marketingscience.comAddress:437 South Rexford DriveBeverly Hills, CA 89377
Look and feel
Each slider illustrates characteristics of the customer's brand and the style your logo design should communicate.

```html
<!DOCTYPE html>
<html lang="en">
<head>
<meta charset="utf-8">
<title>Bright Horizon Guild – Business Card</title>
<link rel="stylesheet" href="https://fonts.googleapis.com/css2?family=Roboto:wght@400;700&family=Roboto+Condensed:wght@700&display=swap">
<style>
  :root {
    --backdrop: #3a302c;
    --card-white: #f7f7f7;
    --card-black: #121212;
    --brand-red: #8e1b1b;
    --ink-grey: #4a4a4a;
    --soft-grey: #6b6b6b;
    --arc-grey: #5a5a5a;
    --gloss: #262626;
    --name-white: #ffffff;
  }
  * { margin: 0; padding: 0; box-sizing: border-box; }
  html, body { width: 1200px; height: 716px; overflow: hidden; }
  body {
    background: var(--backdrop);
    font-family: "Roboto", Arial, sans-serif;
    position: relative;
  }
  .card {
    position: absolute;
    top: 215px;
    width: 500px;
    height: 286px;
    overflow: hidden;
    box-shadow: 0 10px 24px rgba(0,0,0,.45);
  }
  /* Back of card */
  .card--back {
    left: 70px;
    background: var(--card-black);
    display: flex;
    align-items: center;
    justify-content: center;
  }
  .back-wordmark {
    font-family: "Roboto Condensed", "Arial Narrow", sans-serif;
    font-weight: 700;
    font-size: 34px;
    letter-spacing: 1px;
    text-transform: uppercase;
    color: var(--gloss);
  }
  /* Front of card */
  .card--front {
    left: 630px;
    background: var(--card-white);
  }
  .front-shapes { position: absolute; inset: 0; }
  .wordmark {
    position: absolute;
    left: 30px;
    top: 52px;
    display: flex;
    align-items: center;
    gap: 12px;
  }
  .wordmark-dot {
    width: 14px; height: 14px;
    background: var(--brand-red);
  }
  .wordmark-name {
    font-family: "Roboto Condensed", "Arial Narrow", sans-serif;
    font-weight: 700;
    font-size: 21px;
    line-height: 1.02;
    text-transform: uppercase;
    color: var(--ink-grey);
    border-left: 1.5px solid var(--ink-grey);
    padding-left: 12px;
  }
  .holder {
    position: absolute;
    right: 22px;
    top: 88px;
    text-align: right;
    color: var(--name-white);
  }
  .holder-name { font-weight: 700; font-size: 17px; }
  .holder-title { font-size: 10px; margin-top: 4px; }
  .contact-list {
    position: absolute;
    left: 30px;
    top: 150px;
    list-style: none;
    font-size: 11.5px;
    color: var(--soft-grey);
  }
  .contact-list li {
    display: flex;
    align-items: center;
    gap: 8px;
    height: 17px;
  }
  .contact-list svg { width: 10px; height: 10px; fill: var(--brand-red); }
  .contact-list .address { margin-top: 2px; }
</style>
</head>
<body>
  <section class="card card--back" aria-label="Card back">
    <span class="back-wordmark">Bright Horizon Guild</span>
  </section>

  <section class="card card--front" aria-label="Card front">
    <svg class="front-shapes" viewBox="0 0 500 286" preserveAspectRatio="none" aria-hidden="true">
      <path d="M185 0 H500 V215 C440 228 385 190 345 120 C305 55 255 12 185 0 Z" fill="var(--brand-red)"/>
      <path d="M95 24 C190 6 270 22 330 80 C300 50 240 18 150 20 Z" fill="var(--arc-grey)"/>
    </svg>

    <div class="wordmark">
      <span class="wordmark-dot"></span>
      <span class="wordmark-name">Bright<br>Horizon<br>Guild</span>
    </div>

    <div class="holder">
      <div class="holder-name">Neil P. Barton</div>
      <div class="holder-title">CEO</div>
    </div>

    <ul class="contact-list">
      <li><svg viewBox="0 0 10 10"><path d="M1 3 C1 1 3 1 5 1 C7 1 9 1 9 3 L7 4 L6 3 H4 L3 4 Z M2 5 H8 V9 H2 Z"/></svg>310-555-0182</li>
      <li><svg viewBox="0 0 10 10"><path d="M0 2 H10 V8 H0 Z M0 2 L5 6 L10 2" /></svg>neil@brighthorizonguild.com</li>
      <li><svg viewBox="0 0 10 10"><circle cx="5" cy="5" r="4.5"/></svg>www.brighthorizonguild.com</li>
      <li class="address">912 North Calloway Lane Beverly Hills, CA 89377</li>
    </ul>
  </section>
</body>
</html>
```